Law Firm Needs Stationery Design and Business Cards

i would like some fresh new ideas for letterhead. current letterhead is attached. the bottom of the letterhead should have the same content as the bottom of the current letterhead. with the dagger (cross) symbol attached at the beginning and referenced by the two names at the top. see existing letterhead and this will make better sense.

use existing logo and content. nothing overly fancy. i like simple, classy, and refined. does not have to be same font on existing letterhead.

for envelopes, use logo and Raleigh, NC address only

Industry/Entity Type

Business

Contact Information for Business Card

Name: Dominic R. Halvey, Esq.

2784 Bramble Court, Suite 406
Raleigh, NC 27654

phone 919-555-0147
fax 919-555-0183
cell 919-555-0126

www.halveylegalpc.com
dom@halveylegalpc.com

```html
<!DOCTYPE html>
<html lang="en">
<head>
<meta charset="utf-8">
<title>Halvey Legal — Stationery</title>
<link rel="stylesheet" href="https://fonts.googleapis.com/css2?family=Cinzel:wght@600&family=Montserrat:wght@400;600;700&display=swap">
<style>
  :root {
    --navy: #1c2b7f;
    --navy-deep: #16246b;
    --navy-soft: #22348c;
    --grey: #8a8a8d;
    --grey-bar: #7d7d80;
    --paper: #f2f2f2;
    --ink: #3a3a3a;
    --backdrop: #dcdcdc;
  }
  * { box-sizing: border-box; margin: 0; padding: 0; }
  html, body { width: 1200px; height: 1000px; overflow: hidden; }
  body {
    background: var(--backdrop);
    font-family: "Montserrat", sans-serif;
    color: var(--ink);
    position: relative;
  }
  .piece { position: absolute; overflow: hidden; }

  /* brand lockup */
  .brand { position: absolute; display: flex; flex-direction: column; align-items: center; }
  .brand-dot { border-radius: 50%; background: var(--navy); }
  .brand-name {
    font-family: "Cinzel", serif; font-weight: 600; color: var(--navy);
    text-align: center; line-height: 1.1; letter-spacing: 0.04em;
  }
  .brand-name span { display: block; letter-spacing: 0.3em; }
  .brand.on-navy .brand-dot { background: #ffffff; }
  .brand.on-navy .brand-name { color: #ffffff; }

  .ring { position: absolute; border-radius: 50%; border-style: solid; }

  /* letterhead */
  .letterhead { left: 140px; top: 82px; width: 448px; height: 580px; background: var(--paper); }
  .letterhead::before { content: ""; position: absolute; left: 0; right: 0; top: 0; height: 5px; background: var(--grey-bar); }
  .letterhead::after { content: ""; position: absolute; left: 0; right: 0; bottom: 0; height: 6px; background: var(--navy); }
  .letter-body { position: absolute; left: 25px; top: 186px; width: 384px; font-size: 5.9px; line-height: 8px; text-align: justify; }
  .letter-body p { margin-bottom: 8px; }
  .letter-body .salute { font-weight: 700; margin-bottom: 9px; }
  .letter-close { position: absolute; left: 25px; top: 376px; font-size: 5.9px; line-height: 8px; }
  .letter-close strong { font-weight: 700; display: block; }
  .signature { position: absolute; left: 95px; top: 378px; width: 96px; height: 44px;
    background: linear-gradient(100deg, rgba(40,60,170,0.08), rgba(40,60,170,0.22), rgba(40,60,170,0.08)); border-radius: 4px; }
  .letter-footer { position: absolute; left: 25px; top: 534px; display: flex; font-size: 5.2px; line-height: 7px; }
  .letter-footer .col { padding-right: 10px; }
  .letter-footer .col + .col { border-left: 1px solid #c8c8c8; padding-left: 6px; }
  .letter-footer .who { color: var(--navy); font-weight: 700; text-transform: uppercase; }
  .letter-footer b { font-weight: 700; }

  /* business cards */
  .card-front { left: 640px; top: 82px; width: 156px; height: 105px; background: var(--paper); }
  .card-front::before { content: ""; position: absolute; left: 0; right: 0; top: 0; height: 4px; background: var(--grey-bar); }
  .card-front::after { content: ""; position: absolute; left: 0; right: 0; bottom: 0; height: 3px; background: var(--navy); }
  .card-details { position: absolute; right: 9px; top: 12px; text-align: right; font-size: 4.2px; line-height: 5.4px; }
  .card-details .who { color: var(--navy); font-weight: 700; font-size: 5.2px; text-transform: uppercase; }
  .card-details .contact { margin-top: 34px; }
  .card-details .address { margin-top: 4px; }
  .card-back { left: 874px; top: 82px; width: 186px; height: 105px; background: var(--navy); }

  /* folder */
  .folder { left: 639px; top: 238px; width: 464px; height: 602px; background: var(--navy); border-radius: 4px; }
  .folder-spine { position: absolute; left: 22px; top: 0; bottom: 0; width: 2px; background: var(--navy-deep); }

  /* envelope */
  .envelope { left: 87px; top: 713px; width: 501px; height: 217px; background: var(--paper); }
  .envelope::before { content: ""; position: absolute; left: 0; right: 0; top: 0; height: 5px; background: var(--grey-bar); }
  .envelope::after { content: ""; position: absolute; left: 0; right: 0; bottom: 0; height: 6px; background: var(--navy); }
  .envelope-address { position: absolute; left: 26px; top: 191px; font-size: 5.2px; line-height: 6.5px; }
</style>
</head>
<body>

<section class="piece letterhead">
  <div class="brand" style="left:174px; top:26px; width:100px;">
    <div class="brand-dot" style="width:34px; height:34px;"></div>
    <div class="brand-name" style="font-size:16px; margin-top:6px;">Halvey<span style="font-size:7px;">Legal</span></div>
  </div>

  <div class="letter-body">
    <p class="salute">Dear sir,</p>
    <p>Good correspondence remains a quiet mark of care in any practice. A letter carries tone, intent and detail in a form the reader can hold, file and return to later. It sets the terms of a conversation and shows that each word has been weighed before it was sent out to a client, a court or a colleague across town. Messages and calls are quick, yet the written page still holds its place in legal work.</p>
    <p>Today most notes travel by email or text, and paper can seem slow beside them. Still, agencies, lenders and courts rely on signed letters as a lasting record. A printed page is hard to dispute, easy to archive and clear about who wrote it and when. For that reason a firm benefits from stationery that looks settled, calm and consistent on every sheet.</p>
    <p>A letter speaks for the person or office behind it. Take care that the language suits the occasion and the reader. Since a letter may later serve as proof, leave out anything that should not become part of the record, and review each line before signing.</p>
    <p>Writing a clear letter is a skill. The templates we keep on file give everyone a sound base to build on, so each reply can be shaped to its purpose while the layout stays the same.</p>
  </div>

  <div class="letter-close">Yours Sincerely,<strong>Nora Pellison</strong></div>
  <div class="signature" role="img" aria-label="Handwritten signature"></div>

  <footer class="letter-footer">
    <div class="col">
      <div class="who">Dominic R. Halvey, Esq.</div>
      Licensed in NC and FL<br>Board certified Civil trial specialist&dagger;
    </div>
    <div class="col">
      <div class="who">Warren T. Ashby, Esq.</div>
      Of counsel<br>Licensed in FL and GA<br>Board Certified civil trial specialist&dagger;
    </div>
    <div class="col">
      2784 Bramble Court, Suite 406<br>Raleigh, NC 27654<br><b>T:</b> 919.555.0147 · <b>F:</b> 919.555.0183<br>www.halveylegalpc.com
    </div>
    <div class="col">
      318 W. Larkin Avenue<br>Orlando, FL 32809<br><b>T:</b> 321.555.0192<br><b>F:</b> 919.555.0183
    </div>
  </footer>
</section>

<section class="piece card-front">
  <div class="brand" style="left:10px; top:24px; width:70px;">
    <div class="brand-dot" style="width:28px; height:28px;"></div>
    <div class="brand-name" style="font-size:10.5px; margin-top:4px;">Halvey<span style="font-size:5px;">Legal</span></div>
  </div>
  <div class="card-details">
    <div class="who">Dominic R. Halvey, Esq.</div>
    Licensed in NC and FL<br>Board certified Civil trial specialist&dagger;
    <div class="contact"><b>T:</b> 919.555.0147<br><b>F:</b> 919.555.0183<br><b>C:</b> 919.555.0126<br>www.halveylegalpc.com</div>
    <div class="address">2784 Bramble Court, Suite 406<br>Raleigh, NC 27654</div>
  </div>
</section>

<section class="piece card-back">
  <div class="ring" style="left:96px; top:-4px; width:114px; height:114px; border-width:7px; border-color:var(--navy-soft);"></div>
  <div class="brand on-navy" style="left:-5px; top:24px; width:70px;">
    <div class="brand-dot" style="width:28px; height:28px;"></div>
    <div class="brand-name" style="font-size:10.5px; margin-top:4px;">Halvey<span style="font-size:5px;">Legal</span></div>
  </div>
</section>

<section class="piece folder">
  <div class="folder-spine"></div>
  <div class="ring" style="left:88px; top:327px; width:330px; height:330px; border-width:18px; border-color:var(--navy-soft);"></div>
  <div class="brand on-navy" style="left:163px; top:96px; width:180px;">
    <div class="brand-dot" style="width:64px; height:64px;"></div>
    <div class="brand-name" style="font-size:27px; margin-top:22px;">Halvey<span style="font-size:12px;">Legal</span></div>
  </div>
</section>

<section class="piece envelope">
  <div class="ring" style="left:274px; top:44px; width:214px; height:214px; border-width:12px; border-color:#e6e6e6;"></div>
  <div class="brand" style="left:20px; top:18px; width:80px;">
    <div class="brand-dot" style="width:30px; height:30px;"></div>
    <div class="brand-name" style="font-size:14px; margin-top:5px;">Halvey<span style="font-size:6.5px;">Legal</span></div>
  </div>
  <div class="envelope-address">2784 Bramble Court, Suite 406<br>&nbsp;&nbsp;&nbsp;&nbsp;&nbsp;&nbsp;&nbsp;Raleigh, NC 27654</div>
</section>

</body>
</html>
```